RTavenor Business Cards & Letterhead

I have a logo but need a design for some new business cards. We are a Design-Build Firm that specializes in the design and construction of commercial projects.
the cards need to be professional. no cartoon stuff.
i would like to have the cards in AI format so I can update the card as needed. Logo is provided.
Our Address is: 4187 Marlowe Ct. Linwood, West Fairmont 27614

```html
<!DOCTYPE html>
<html lang="en">
<head>
<meta charset="utf-8">
<title>RTavenor Business Card</title>
<link rel="stylesheet" href="https://fonts.googleapis.com/css2?family=Arimo:wght@400;700&display=swap">
<style>
  :root {
    --backdrop: #2b2b2d;
    --brand-blue: #0a6aa8;
    --brand-blue-deep: #04508a;
    --brand-blue-light: #1480c2;
    --paper: #f6f6f6;
    --ink: #2f3033;
    --divider: #3a3c40;
    --on-blue: #ffffff;
    --on-blue-soft: #d6e7f4;
  }
  * { box-sizing: border-box; margin: 0; padding: 0; }
  html, body { width: 1200px; height: 947px; overflow: hidden; }
  body {
    background: var(--backdrop);
    font-family: "Arimo", Arial, sans-serif;
    position: relative;
  }
  .card {
    position: absolute;
    width: 560px;
    height: 320px;
    border-radius: 22px;
    overflow: hidden;
    box-shadow: 0 14px 30px rgba(0,0,0,0.45);
  }
  .card-back {
    left: 60px;
    top: 150px;
    background: radial-gradient(ellipse at 55% 40%, var(--brand-blue-light), var(--brand-blue) 55%, var(--brand-blue-deep));
    display: flex;
    align-items: center;
    justify-content: center;
  }
  .card-front {
    left: 580px;
    top: 477px;
    display: flex;
    background: var(--paper);
  }
  .brand-name {
    font-weight: 700;
    letter-spacing: 1px;
    text-transform: uppercase;
    display: flex;
    align-items: center;
    gap: 10px;
  }
  .card-back .brand-name { color: var(--on-blue); font-size: 52px; }
  .card-back .brand-mark { width: 34px; height: 34px; background: var(--on-blue); }
  .front-brand {
    width: 250px;
    display: flex;
    align-items: center;
    justify-content: center;
    background: var(--paper);
  }
  .front-brand .brand-name { color: var(--ink); font-size: 30px; }
  .front-brand .brand-mark { width: 20px; height: 20px; background: var(--brand-blue); }
  .divider { width: 5px; background: var(--divider); }
  .contact-panel {
    flex: 1;
    background: radial-gradient(ellipse at 40% 30%, var(--brand-blue-light), var(--brand-blue) 60%, var(--brand-blue-deep));
    color: var(--on-blue);
    padding: 58px 0 0 40px;
  }
  .person-name { font-size: 21px; font-weight: 700; }
  .person-title { font-size: 12px; color: var(--on-blue-soft); margin-top: 2px; }
  .address { font-size: 14px; line-height: 18px; margin-top: 14px; }
  .contact-list { list-style: none; margin-top: 10px; font-size: 14px; line-height: 19px; }
  .contact-list li { display: flex; align-items: center; gap: 8px; }
  .contact-list svg { width: 12px; height: 12px; flex: none; }
</style>
</head>
<body>
  <section class="card card-back">
    <div class="brand-name"><span class="brand-mark"></span>RTavenor</div>
  </section>

  <section class="card card-front">
    <div class="front-brand">
      <div class="brand-name"><span class="brand-mark"></span>RTavenor</div>
    </div>
    <div class="divider"></div>
    <div class="contact-panel">
      <div class="person-name">Daniel Whitford</div>
      <div class="person-title">Managing Director</div>
      <div class="address">4187 Marlowe Ct. Linwood<br>West Fairmont 27614</div>
      <ul class="contact-list">
        <li><svg viewBox="0 0 12 12"><path d="M2.5 1 L4.5 1 L5.2 3.6 L4 4.6 Q5 7 7.4 8 L8.4 6.8 L11 7.5 L11 9.5 Q10.5 11 9 11 Q1 10 1 3 Q1 1.5 2.5 1 Z" fill="#fff"/></svg>919-555-0142</li>
        <li><svg viewBox="0 0 12 12"><rect x="3" y="0.8" width="6" height="10.4" rx="1" fill="none" stroke="#fff" stroke-width="1.2"/><circle cx="6" cy="9.4" r="0.7" fill="#fff"/></svg>919-555-0187</li>
        <li><svg viewBox="0 0 12 12"><rect x="0.8" y="2.5" width="10.4" height="7" fill="none" stroke="#fff" stroke-width="1.1"/><path d="M0.8 2.5 L6 6.6 L11.2 2.5" fill="none" stroke="#fff" stroke-width="1.1"/></svg>info@rtavenor.com</li>
        <li><svg viewBox="0 0 12 12"><circle cx="6" cy="6" r="5" fill="none" stroke="#fff" stroke-width="1.1"/><ellipse cx="6" cy="6" rx="2.2" ry="5" fill="none" stroke="#fff" stroke-width="0.9"/><path d="M1 6 H11" stroke="#fff" stroke-width="0.9"/></svg>www.rtavenor.com</li>
      </ul>
    </div>
  </section>
</body>
</html>
```